Velvet Pressings Techno Label Business Card

I'm looking for a very clean business card for my Velvet Pressings music label. The label focusses on techno music. The card should include:

• my name : Tomas Brandt as "Founder & CEO"
• email address: tomas@velvet-pressings.example
• web: www.velvet-pressings.example
• facebook logo + /velvetpress
• twitter logo + /velvetpress
• soundcloud logo + /velvetpressings

Feel free to include your ideas! I'm looking forward to discuss about it.

Tomas

Industry/Entity Type

Business

Contact Information for Business Card

I don't like glossy cards. Prefer matt.

Requirements
Nice to have
• Maybe on one side the complete logo, other side just the icon.
Should not have
• Flashy stuff. Must be clean and business like style.

```html
<!DOCTYPE html>
<html lang="en">
<head>
<meta charset="utf-8">
<title>Velvet Pressings — Business Card</title>
<link rel="stylesheet" href="https://fonts.googleapis.com/css2?family=Open+Sans:wght@400;600;700&display=swap">
<style>
  :root {
    --brand-orange: #f26a1b;
    --brand-orange-faint: #fbd9c4;
    --ink-grey: #6d6e71;
    --ink-light: #8a8b8e;
    --card-white: #ffffff;
    --backdrop: #e9e5df;
  }
  * { box-sizing: border-box; margin: 0; padding: 0; }
  html, body {
    width: 1200px;
    height: 799px;
    overflow: hidden;
    background: var(--backdrop);
    font-family: "Open Sans", Arial, sans-serif;
  }
  .card-set {
    position: absolute;
    inset: 0;
    display: flex;
    align-items: center;
    justify-content: center;
    gap: 60px;
  }
  .card {
    position: relative;
    width: 520px;
    height: 297px;
    background: var(--card-white);
    overflow: hidden;
    box-shadow: 0 2px 6px rgba(0,0,0,0.12);
  }

  /* Back: mark only */
  .card-back .brand-mark {
    position: absolute;
    left: 50%;
    top: 46%;
    transform: translate(-50%, -50%);
    display: flex;
    align-items: center;
    gap: 14px;
  }
  .brand-dot {
    width: 34px;
    height: 34px;
    border-radius: 50%;
    background: var(--brand-orange);
    flex: none;
  }
  .brand-name {
    color: var(--brand-orange);
    font-weight: 700;
    font-size: 30px;
    letter-spacing: -0.3px;
    white-space: nowrap;
  }
  .card-back .back-url {
    position: absolute;
    right: 34px;
    bottom: 30px;
    color: var(--ink-grey);
    font-size: 11px;
    letter-spacing: 0.3px;
  }

  /* Front: details */
  .card-front .faint-disc {
    position: absolute;
    right: -70px;
    top: -70px;
    width: 240px;
    height: 240px;
    border-radius: 50%;
    background: var(--brand-orange-faint);
    opacity: 0.55;
  }
  .card-front .front-brand {
    position: absolute;
    left: 30px;
    top: 30px;
    display: flex;
    align-items: center;
    gap: 10px;
  }
  .card-front .front-brand .brand-dot { width: 24px; height: 24px; }
  .card-front .front-brand .brand-name { font-size: 22px; }

  .person {
    position: absolute;
    left: 30px;
    top: 104px;
  }
  .person-name {
    color: var(--brand-orange);
    font-weight: 700;
    font-size: 19px;
    line-height: 1.1;
  }
  .person-role {
    color: var(--ink-grey);
    font-size: 13px;
    margin-top: 2px;
  }

  .contact-list {
    position: absolute;
    left: 30px;
    top: 166px;
    list-style: none;
    font-size: 12px;
    line-height: 19px;
    color: var(--ink-grey);
  }
  .contact-key {
    color: var(--brand-orange);
    font-weight: 700;
    display: inline-block;
    width: 22px;
  }

  .social-row {
    position: absolute;
    left: 30px;
    bottom: 26px;
    display: flex;
    align-items: center;
    gap: 18px;
    color: var(--ink-grey);
    font-size: 12px;
  }
  .social-item { display: flex; align-items: center; gap: 6px; }
  .social-dot {
    width: 22px;
    height: 22px;
    border-radius: 50%;
    border: 2px solid var(--ink-light);
    flex: none;
  }
</style>
</head>
<body>
  <main class="card-set">
    <section class="card card-back" aria-label="Card back">
      <div class="brand-mark">
        <span class="brand-dot"></span>
        <span class="brand-name">Velvet Pressings</span>
      </div>
      <p class="back-url">www.velvet-pressings.example</p>
    </section>

    <section class="card card-front" aria-label="Card front">
      <div class="faint-disc" aria-hidden="true"></div>
      <div class="front-brand">
        <span class="brand-dot"></span>
        <span class="brand-name">Velvet Pressings</span>
      </div>

      <div class="person">
        <p class="person-name">Tomas Brandt</p>
        <p class="person-role">Founder &amp; CEO</p>
      </div>

      <ul class="contact-list">
        <li><span class="contact-key">T :</span>(555) 014-2297</li>
        <li><span class="contact-key">E :</span>tomas@velvet-pressings.example</li>
        <li><span class="contact-key">W :</span>www.velvet-pressings.example</li>
      </ul>

      <div class="social-row">
        <span class="social-item"><span class="social-dot" aria-hidden="true"></span>/velvetpress</span>
        <span class="social-item"><span class="social-dot" aria-hidden="true"></span>/velvetpress</span>
        <span class="social-item"><span class="social-dot" aria-hidden="true"></span>/velvetpressings</span>
      </div>
    </section>
  </main>
</body>
</html>
```